NEW Wordpress Website Design for a Dynamic Long Term Healthcare Company in Hawaii

I would like a new website design for my current company, Marlow Health Collective, which has two different brands - Marlow Homecare and Marlow Senior Living. You can see the current website at www.marlowhealth-example.com. The website should be built using Wordpress Software and the Framewise theme. The website should have a local Hawaii island/tropical feel, but look professional for healthcare. I'm looking for something fresh, and want the designer to select colors, styles, etc.

In the Header, on all pages, I would like a menu that includes Home Care, Senior Living, Rates, and About Us.
Under each of the Header Menu Titles, I would like these drop downs included:
Home Care (drop down pages)- Nurse Aide Care, 24-Hour Home Care, Skilled Nursing, Lifestyle Aide, Hospice at Home, Bathing & Meal Service.
Senior Living (drop down pages) - Long-Term Stay, Short-Term Stay.
Rates (drop down page) - Rates.
About Us (drop down pages) - Our Mission, Ohana Talk, About Dana Marlow.

In the footer, on all pages, you should include the address: 248 Pueo Lane, Suite 310, Honolulu, HI 96817. Phone number: 808-555-0172
The footer should also include buttons for a page called Learn, Caregiver Jobs, and each of the service page links to include: Nurse Aide Care, 24-Hour Home Care, Skilled Nursing, Lifestyle Aide, Hospice at Home, Bathing & Meal Service.
Please don't take the current website and redesign a few aspects. I'm looking for a completely different look and feel.

Target Market(s)

40-80 year olds

Industry/Entity Type

Long Term Healthcare

Coding

Coded - Design and coding required

Requirements
Should not have
• Our existing website as a template. We are looking for a complete redesign. Thank you.

```html
<!DOCTYPE html>
<html lang="en">
<head>
<meta charset="utf-8">
<title>Marlow Health Collective — Homecare and Senior Living in Hawaii</title>
<link rel="stylesheet" href="https://fonts.googleapis.com/css2?family=Montserrat:wght@700;800&family=Nunito:wght@400;600;700&display=swap">
<style>
:root{
  --teal:#1d5a52;
  --teal-deep:#174a44;
  --coral:#f4796b;
  --coral-soft:#f08f83;
  --paper:#e9e8e6;
  --card:#e6e5e3;
  --field:#d8dcda;
  --ink:#151515;
  --muted:#555;
  --white:#ffffff;
}
*{box-sizing:border-box;margin:0;padding:0}
html,body{width:1200px;height:3531px;overflow:hidden}
body{position:relative;background:var(--paper);font-family:"Nunito",sans-serif;color:var(--ink)}
.abs{position:absolute}
.bg{z-index:0}
.btn{position:absolute;z-index:3;display:flex;align-items:center;justify-content:center;border-radius:30px;font-family:"Nunito",sans-serif;font-weight:600;font-size:18px;color:var(--white);white-space:nowrap}
.btn--teal{background:var(--teal)}
.btn--coral{background:var(--coral)}
.heading{font-family:"Montserrat",sans-serif;font-weight:800;text-transform:uppercase;letter-spacing:.5px}

/* hero */
.hero-photo{left:0;top:0;width:1200px;height:940px;
  background:linear-gradient(180deg,#2f6fc4 0%,#7fb0de 12%,#cfe0ee 22%,#4f8a5a 30%,#3a9fa6 40%,#9fd6cf 50%,#d9dcd7 62%,var(--paper) 75%,var(--paper) 100%)}
.hero-photo::before{content:"";position:absolute;left:0;top:0;width:600px;height:600px;background:radial-gradient(ellipse 420px 460px at 0 120px,rgba(46,107,46,.85) 0%,rgba(77,138,58,.5) 55%,rgba(77,138,58,0) 100%)}
.menu-toggle{left:1094px;top:40px;width:61px;height:60px;background:var(--teal);border-radius:6px;z-index:2}
.menu-toggle span{position:absolute;right:16px;height:2px;background:var(--coral);border-radius:2px}
.brand-card{left:255px;top:352px;width:689px;height:280px;background:var(--card);border-radius:22px;box-shadow:0 6px 18px rgba(0,0,0,.12);z-index:2}
.brand{position:absolute;z-index:2;display:flex;flex-direction:column;align-items:center;gap:12px;font-family:"Nunito",sans-serif;font-weight:700;font-size:26px;color:var(--teal);text-align:center;line-height:1.15}
.brand i{display:block;width:52px;height:52px;border-radius:10px}
.hero-title{left:0;top:688px;width:1200px;text-align:center;font-size:52px;line-height:64px;z-index:2}
.hero-lead{left:180px;top:830px;width:840px;text-align:center;font-size:20px;line-height:36px;color:var(--muted);z-index:2}

/* about */
.about-scene{left:0;top:940px;width:1200px;height:692px;
  background:linear-gradient(180deg,var(--paper) 0%,#c9cfc6 18%,#9aab87 45%,#4d6d34 80%,#3b5a2a 100%)}
.about-scene::after{content:"";position:absolute;inset:0;background:radial-gradient(ellipse 420px 300px at 830px 300px,rgba(240,240,238,.85),rgba(240,240,238,0))}
.photo-circle{border-radius:50%;z-index:2}
.photo-main{left:111px;top:1086px;width:420px;height:420px;background:radial-gradient(circle at 40% 40%,#e7d98a,#c99a55 60%,#9c6b3c)}
.photo-small{left:393px;top:1320px;width:184px;height:184px;background:radial-gradient(circle at 50% 40%,#d9d27a,#5fa8c2 70%);border:6px solid #e9e9e9;z-index:3}
.about-title{left:636px;top:1132px;font-size:40px;z-index:2}
.about-text{left:636px;top:1202px;width:460px;font-size:16px;line-height:31px;color:var(--muted);z-index:2}

/* split */
.split{top:1632px;width:600px;height:470px;color:var(--white);text-align:center;z-index:1}
.split--home{left:0;background:var(--teal);border-bottom-right-radius:96px}
.split--senior{left:600px;background:var(--coral-soft);border-bottom-left-radius:96px}
.split h2{position:absolute;top:98px;left:0;width:100%;font-size:44px;color:var(--white)}
.split p{position:absolute;top:160px;left:60px;width:480px;font-size:16px;line-height:30px}
.split .btn{top:313px;left:151px;width:299px;height:48px}

/* contact */
.contact-title{left:0;top:2176px;width:1200px;text-align:center;font-size:40px}
.field{position:absolute;left:141px;width:443px;height:58px;background:var(--field);border-radius:30px;padding:0 30px;display:flex;align-items:center;justify-content:space-between;font-size:15px;color:#555}
.field svg{width:16px;height:16px;fill:#555}
.field--comments{left:614px;top:2261px;height:294px;align-items:flex-start;padding-top:20px;border-radius:30px}

/* brands row */
.brands-row .brand{top:2642px;width:300px}

/* footer */
.ocean{left:0;top:2825px;width:1200px;height:706px;
  background:linear-gradient(180deg,var(--paper) 0%,#d6e6e4 8%,#8ad0d3 20%,#2aa3b5 38%,#11819a 58%,#0a6d86 80%,#0b5e7a 100%)}
.services{left:0;top:3218px;width:1200px;display:flex;justify-content:center;gap:48px;font-size:17px;font-weight:600;color:var(--white);z-index:2}
.icon-dot{width:56px;height:56px;border-radius:50%;background:var(--coral);display:flex;align-items:center;justify-content:center;z-index:2}
.icon-dot svg{width:18px;height:18px;fill:var(--white)}
.info{width:320px;text-align:center;font-size:17px;font-weight:700;line-height:30px;color:var(--white);z-index:2}
.btn--white{background:var(--white);color:var(--coral)}
.rule{left:112px;top:3464px;width:976px;height:1px;background:rgba(255,255,255,.6);z-index:2}
.copyright{left:0;top:3492px;width:1200px;text-align:center;font-size:16px;color:var(--white);z-index:2}
</style>
</head>
<body>

<header>
  <div class="abs bg hero-photo" role="img" aria-label="Tropical beach with palm trees, green mountains, turquoise sea and blue sky"></div>
  <nav class="abs menu-toggle" aria-label="Main menu">
    <span style="top:20px;width:24px"></span>
    <span style="top:29px;width:30px"></span>
    <span style="top:38px;width:20px"></span>
  </nav>
  <div class="abs brand-card">
    <div class="brand" style="left:60px;top:64px;width:240px"><i style="background:#5fa19c"></i>Marlow<br>Senior Living</div>
    <div class="brand" style="left:370px;top:56px;width:240px"><i style="background:var(--coral)"></i>Marlow<br>Homecare</div>
  </div>
  <h1 class="abs heading hero-title">Hawaii's Choice<br>Homecare and Senior</h1>
  <p class="abs hero-lead">Marlow Homecare provides a variety of professional in-home health care services throughout the entire island of Oahu.</p>
</header>

<section class="about">
  <div class="abs bg about-scene" role="img" aria-label="Misty green Hawaiian valley and mountain ridges at sunrise"></div>
  <a class="btn btn--teal" style="left:351px;top:924px;width:299px;height:49px">Schedule Care Assessment</a>
  <a class="btn btn--coral" style="left:677px;top:924px;width:169px;height:49px">Get Started</a>
  <div class="abs photo-circle photo-main" role="img" aria-label="Caregiver and senior client chatting on a sofa at home"></div>
  <div class="abs photo-circle photo-small" role="img" aria-label="Nurse assisting an elderly man at home"></div>
  <h2 class="abs heading about-title">About Us</h2>
  <p class="abs about-text">At Marlow Health Collective, our mission is to provide compassionate and professional long-term healthcare services that empower individuals to maintain their highest level of independence, health, and well-being in the comfort of their own homes or ours, either through our licensed home healthcare agency</p>
  <a class="btn btn--coral" style="left:636px;top:1408px;width:136px;height:39px;font-size:16px">Read More</a>
</section>

<section>
  <div class="abs split split--home">
    <h2 class="heading">Home Care</h2>
    <p>Marlow Homecare understands that every person's care journey is unique. We tailor our in-home services to meet the diverse nurturing experience of professional quality care and safety within the comfort and convenience of your own home.</p>
    <a class="btn btn--coral">Schedule Care Assessment</a>
  </div>
  <div class="abs split split--senior">
    <h2 class="heading">Senior Living</h2>
    <p>Marlow Senior Living creates a warm, supportive, and enriching care home environment where seniors can thrive in their golden years. We provide residential care that promotes well-being, connection, and dignity of each individual.</p>
    <a class="btn btn--teal">Schedule Care Assessment</a>
  </div>
</section>

<section class="contact">
  <h2 class="abs heading contact-title">Get in Touch With Us</h2>
  <div class="field" style="top:2261px">Full Name<svg viewBox="0 0 16 16"><circle cx="8" cy="5" r="3.5"/><path d="M1.5 15c0-4 3-6 6.5-6s6.5 2 6.5 6z"/></svg></div>
  <div class="field" style="top:2340px">Email Address<svg viewBox="0 0 16 16"><path d="M1 3h14v10H1z"/><path d="M1 3l7 6 7-6" fill="none" stroke="#d8dcda" stroke-width="1.4"/></svg></div>
  <div class="field" style="top:2418px">Contact Number<svg viewBox="0 0 16 16"><path d="M3 1l3 0 1 4-2 1c1 2 3 4 5 5l1-2 4 1v3c0 1-1 2-2 2C7 15 1 9 1 3c0-1 1-2 2-2z"/></svg></div>
  <a class="btn btn--coral" style="left:141px;top:2497px;width:443px;height:58px">Send Message</a>
  <div class="field field--comments">Comments<svg viewBox="0 0 16 16"><path d="M2 2h12v8H7l-3 3v-3H2z"/></svg></div>
</section>

<section class="brands-row">
  <div class="brand" style="left:149px"><i style="background:#5fa19c"></i>Marlow<br>Senior Living</div>
  <div class="brand" style="left:450px;color:var(--ink)"><i style="background:var(--ink)"></i>Marlow<br>Health Collective</div>
  <div class="brand" style="left:732px"><i style="background:var(--coral)"></i>Marlow<br>Homecare</div>
</section>

<footer>
  <div class="abs bg ocean" role="img" aria-label="Aerial view of turquoise ocean waves breaking on white sand"></div>
  <ul class="abs services" style="list-style:none">
    <li>Nurse Aide Care</li><li>24-Hour Home Care</li><li>Skilled Nursing</li><li>Lifestyle Aide</li><li>Hospice at Home</li><li>Bathing &amp; Meal Service</li>
  </ul>
  <div class="abs icon-dot" style="left:268px;top:3292px"><svg viewBox="0 0 16 16"><path d="M8 1a5 5 0 0 0-5 5c0 4 5 9 5 9s5-5 5-9a5 5 0 0 0-5-5zm0 7a2 2 0 1 1 0-4 2 2 0 0 1 0 4z"/></svg></div>
  <div class="abs icon-dot" style="left:572px;top:3292px"><svg viewBox="0 0 16 16"><path d="M3 1l3 0 1 4-2 1c1 2 3 4 5 5l1-2 4 1v3c0 1-1 2-2 2C7 15 1 9 1 3c0-1 1-2 2-2z"/></svg></div>
  <p class="abs info" style="left:136px;top:3360px">248 Pueo Lane, Suite 310,<br>Honolulu, HI 96817</p>
  <p class="abs info" style="left:440px;top:3360px">Contact Number:<br>808-555-0172 (Phone)</p>
  <a class="btn btn--coral" style="left:780px;top:3294px;width:190px;height:51px">Caregiver Jobs</a>
  <a class="btn btn--white" style="left:780px;top:3360px;width:190px;height:51px">Learn</a>
  <div class="abs rule"></div>
  <p class="abs copyright">(C) Copyright 2024 | All Rights Reserved</p>
</footer>

</body>
</html>
```